Consulting company business cards

We have a base design, but would be willing to update. We have a new logo/"tag" that needs to be added. Current business card design is attached for reference into our "style."

Industry/Entity Type

Business

Contact Information for Business Card

Should contain name and title, office number, mobile number if appropriate, e-mail, website, physical address, and company logo.

Font styles to use
Other font styles liked:
• See current card design on KorvandBCard

Colors
0455a3
85acd3
aaaaaa

Requirements
Must have
• Our colors are navy blue, gray, and a lighter blue
Nice to have
• Design that I can easily drop in new names/titles as we hire employees.

```html
<!DOCTYPE html>
<html lang="en">
<head>
<meta charset="utf-8">
<title>Brenlow Business Card</title>
<link rel="stylesheet" href="https://fonts.googleapis.com/css2?family=Open+Sans:wght@400;600;700&display=swap">
<style>
  :root {
    --stage: #3a3a3a;
    --card: #111213;
    --card-edge: #1c1d1f;
    --navy: #0455a3;
    --navy-deep: #143c5e;
    --light-blue: #85acd3;
    --sky: #7fb1d6;
    --gray: #aaaaaa;
    --text: #e6e6e6;
  }
  * { box-sizing: border-box; margin: 0; padding: 0; }
  html, body { width: 1200px; height: 900px; overflow: hidden; }
  body {
    background: var(--stage);
    font-family: "Open Sans", Arial, sans-serif;
    position: relative;
  }
  .card {
    position: absolute;
    top: 300px;
    width: 520px;
    height: 297px;
    background: var(--card);
    border: 1px solid var(--card-edge);
    border-radius: 22px;
    box-shadow: 0 14px 30px rgba(0,0,0,.35);
    overflow: hidden;
  }
  .card--front { left: 70px; }
  .card--back { left: 610px; }

  /* front */
  .mascot-art {
    position: absolute;
    left: 60px; top: 85px;
    width: 150px; height: 128px;
    border-radius: 48% 40% 30% 42%;
    background: radial-gradient(circle at 45% 40%, #8dbbdd, var(--sky) 70%);
  }
  .divider {
    position: absolute;
    left: 246px; top: 40px;
    width: 1px; height: 217px;
    background: linear-gradient(to bottom, transparent, #3a3c40 30%, #3a3c40 70%, transparent);
  }
  .details {
    position: absolute;
    left: 274px; top: 58px;
    color: var(--text);
    font-size: 13px;
    line-height: 1.4;
  }
  .details__name {
    color: var(--sky);
    font-weight: 700;
    font-size: 18px;
    line-height: 1.2;
  }
  .details__title { margin-bottom: 16px; }
  .details__address { margin-bottom: 14px; }
  .contact { list-style: none; }
  .contact li {
    display: flex; align-items: center; gap: 8px;
    font-size: 14px; line-height: 1.45;
  }
  .contact svg { width: 11px; height: 11px; fill: var(--light-blue); flex: none; }

  /* back */
  .brand {
    position: absolute;
    left: 78px; top: 78px;
    display: flex; align-items: center; gap: 12px;
  }
  .brand__name {
    color: var(--navy-deep);
    font-weight: 700;
    font-size: 52px;
    letter-spacing: 1px;
    line-height: 1;
  }
  .brand__dot {
    width: 40px; height: 40px;
    border-radius: 50%;
    background: var(--sky);
  }
  .tagline {
    position: absolute;
    left: 82px; top: 138px;
    color: var(--gray);
    font-size: 13px;
    letter-spacing: 2.6px;
  }
  .web {
    position: absolute;
    left: 268px; top: 184px;
    color: var(--sky);
    font-size: 13px;
  }
  .rule {
    position: absolute;
    left: 40px; right: 40px; top: 212px;
    height: 1px;
    background: linear-gradient(to right, transparent, var(--navy) 40%, var(--navy) 70%, transparent);
  }
</style>
</head>
<body>
  <section class="card card--front">
    <div class="mascot-art" role="img" aria-label="Light blue illustration of a dog's head in profile"></div>
    <div class="divider"></div>
    <div class="details">
      <p class="details__name">Renata Korvand</p>
      <p class="details__title">Office Manager</p>
      <p class="details__address">1875 W 48TH St Lakemont<br>Ohio 45012</p>
      <ul class="contact">
        <li><svg viewBox="0 0 16 16"><path d="M3 1l3 3-2 2c1 2 3 4 5 5l2-2 3 3-2 3C7 15 1 9 1 3z"/></svg>555.014.2910</li>
        <li><svg viewBox="0 0 16 16"><path d="M4 0h8a1 1 0 011 1v14a1 1 0 01-1 1H4a1 1 0 01-1-1V1a1 1 0 011-1zm1 2v10h6V2zm3 11a1 1 0 100 2 1 1 0 000-2z"/></svg>555.014.2971</li>
        <li><svg viewBox="0 0 16 16"><path d="M0 3h16v10H0zm1 1v1l7 4 7-4V4z"/></svg>rkorvand@brenlowtech.com</li>
        <li><svg viewBox="0 0 16 16"><circle cx="8" cy="8" r="7"/></svg>brenlowtech.com</li>
      </ul>
    </div>
  </section>

  <section class="card card--back">
    <div class="brand">
      <span class="brand__name">BRENLOW</span>
      <span class="brand__dot"></span>
    </div>
    <p class="tagline">A CLOUD CONSULTING COMPANY</p>
    <p class="web">www.brenlowtech.com</p>
    <div class="rule"></div>
  </section>
</body>
</html>
```